Business Card Design

IT Solutions company.

I need a professional looking design with my company logo if possible.

Logo is located here:
http://www.brunelwavesystems.co.uk/dev/images/logo1.jpg
Feel free to redesign the logo if you think you have any better suggestions.

Our services include, IT Infrastructure/Telephony Maintenance & Hosting Services. Linux and Windows Solutions, App Development.

Out website is currently under development:
http://www.brunelwavesystems.co.uk/dev/

I'm looking for a colourful but professional looking business card.

Industry/Entity Type

Business

Contact Information for Business Card

BW Brunel Wavesystems Ltd
Martin Hollisby
07700958312
www.brunelwavesystems.co.uk
mhollisby@brunelwavesystems.co.uk

```html
<!DOCTYPE html>
<html lang="en">
<head>
<meta charset="utf-8">
<title>BW Brunel Wavesystems Ltd – Business Card</title>
<link rel="stylesheet" href="https://fonts.googleapis.com/css2?family=Arimo:wght@400;700&display=swap">
<style>
  :root {
    --page-bg: #1b1b1d;
    --card-white: #ffffff;
    --brand-blue: #1f44b0;
    --brand-black: #111111;
    --ink: #111111;
    --on-dark: #ffffff;
  }
  * { box-sizing: border-box; margin: 0; padding: 0; }
  html, body {
    width: 1200px; height: 1000px; overflow: hidden;
    background: var(--page-bg);
    font-family: "Arimo", Arial, sans-serif;
  }
  .canvas {
    width: 1200px; height: 1000px;
    display: flex; flex-direction: column;
    align-items: center; justify-content: center; gap: 60px;
  }
  .card {
    position: relative; width: 700px; height: 400px;
    background: var(--card-white); overflow: hidden;
  }
  .brand {
    position: absolute;
    color: var(--ink); font-weight: 700; font-size: 17px; letter-spacing: 0.2px;
  }
  /* front */
  .card-front .brand { left: 40px; top: 150px; }
  .name-block {
    position: absolute; left: 0; top: 200px; width: 285px; height: 92px;
    background: var(--brand-black); color: var(--on-dark);
    display: flex; align-items: center; padding-left: 32px;
    font-size: 23px;
  }
  .name-block .first { font-weight: 700; margin-right: 7px; }
  .contact-block {
    position: absolute; left: 285px; top: 292px; width: 370px; height: 92px;
    background: var(--brand-blue); color: var(--on-dark);
    padding: 12px 0 0 22px;
  }
  .company { font-size: 20px; margin-bottom: 6px; }
  .contact-line { display: flex; align-items: center; gap: 8px; font-size: 15px; line-height: 20px; }
  .contact-line svg { width: 14px; height: 14px; flex: none; }
  /* back */
  .back-band {
    position: absolute; left: 0; top: 0; width: 700px; height: 250px;
    background: linear-gradient(135deg, #1c3ea6, #2a55c2);
  }
  .back-accent {
    position: absolute; right: 0; top: 180px; width: 38px; height: 70px;
    background: var(--brand-black);
  }
  .card-back .brand { left: 40px; top: 285px; }
  .web {
    position: absolute; right: 45px; bottom: 38px;
    font-size: 20px; color: var(--ink);
  }
</style>
</head>
<body>
<main class="canvas">
  <section class="card card-front" aria-label="Business card front">
    <div class="brand">BW Brunel Wavesystems Ltd</div>
    <div class="name-block"><span class="first">Martin</span>Hollisby</div>
    <div class="contact-block">
      <p class="company">BW Brunel Wavesystems Ltd</p>
      <p class="contact-line">
        <svg viewBox="0 0 16 16" aria-hidden="true"><rect width="16" height="16" rx="3" fill="#fff"/><path d="M5 3.5c-1.5 1-1.5 3 0 5.5s3.5 4 5.5 3.5l.8-1.6-2-1.2-1 .8c-1-.6-1.8-1.5-2.3-2.5l.9-.9-1-2.1z" fill="#1f44b0"/></svg>
        07700 958312
      </p>
      <p class="contact-line">
        <svg viewBox="0 0 16 16" aria-hidden="true"><rect x="1" y="3" width="14" height="10" fill="#fff"/><path d="M1 3l7 6 7-6" fill="none" stroke="#1f44b0" stroke-width="1.4"/></svg>
        mhollisby@brunelwavesystems.co.uk
      </p>
    </div>
  </section>

  <section class="card card-back" aria-label="Business card back">
    <div class="back-band"></div>
    <div class="back-accent"></div>
    <div class="brand">BW Brunel Wavesystems Ltd</div>
    <p class="web">www.brunelwavesystems.co.uk</p>
  </section>
</main>
</body>
</html>
```